New Business Card for Web Design/Internet Marketing Company

Looking for a great looking new business card. We are a 10 year old web design, internet marketing and website management company that works mostly with small businesses.

Our new card needs to better match the colors and style of our website, be bold, extremely usable and slightly edgy.

Target Market(s)

Small/Medium businesses that have websites

Industry/Entity Type

Internet

Requirements
Must have
• Front and back design, full color, rounded corners please

Must use the colors/style of our website (JPG provided)

INFO FOR CARDS (as readable as possible please)
Mark Lenner
President/CEO
mark@trelvanmedia.example
Phone: 520-381-7459
Toll Free: 866-381-7459
Address: 4315 W. Calloway Ave. Ste. 140, Tucson, AZ 85792

THINGS I WANT TO PROMOTE (if there is room):
1. Our Website - www.trelvanmedia.example

2. Social Media
Twitter: @trelvanmedia
Facebook: www.facebook.com/trelvanmedia

3. Our Services
Web Design
Internet Marketing
Website Management

```html
<!DOCTYPE html>
<html lang="en">
<head>
<meta charset="UTF-8">
<title>Trelvan Media Business Card</title>
<link href="https://fonts.googleapis.com/css2?family=Open+Sans:ital,wght@0,400;0,600;0,700;1,400&family=Yanone+Kaffeesatz:wght@400;600&display=swap" rel="stylesheet">
<style>
  :root {
    --bg: #eef0f5;
    --orange-light: #f3a037;
    --orange-dark: #d9641e;
    --blue-deep: #173e6e;
    --blue-mid: #1f6aa8;
    --blue-bright: #2aa5cf;
    --blue-cyan: #37bfe0;
    --white: #ffffff;
    --ink-soft: #dcecf7;
  }
  * { margin: 0; padding: 0; box-sizing: border-box; }
  html, body { width: 1200px; height: 900px; overflow: hidden; }
  body {
    background: var(--bg);
    font-family: "Open Sans", sans-serif;
    display: flex;
    flex-direction: column;
    align-items: center;
    justify-content: center;
    gap: 50px;
  }
  .card {
    position: relative;
    width: 630px;
    height: 360px;
    border-radius: 22px;
    overflow: hidden;
    box-shadow: 0 12px 30px rgba(20, 40, 70, 0.22);
  }

  /* Front */
  .card-front {
    background: linear-gradient(160deg, var(--blue-mid) 0%, var(--blue-bright) 60%, var(--blue-cyan) 100%);
  }
  .front-art { position: absolute; inset: 0; }
  .brand {
    position: absolute;
    left: 30px;
    top: 50%;
    transform: translateY(-50%);
    width: 190px;
    color: var(--white);
  }
  .brand-row { display: flex; align-items: center; gap: 10px; }
  .brand-dot {
    flex: none;
    width: 30px; height: 30px; border-radius: 50%;
    background: var(--white);
  }
  .brand-name {
    font-family: "Yanone Kaffeesatz", sans-serif;
    font-weight: 600;
    font-size: 42px;
    line-height: 0.95;
  }
  .brand-tagline {
    margin: 8px 0 0 40px;
    font-size: 11px;
    font-style: italic;
    color: var(--white);
  }
  .person {
    position: absolute;
    right: 36px;
    top: 34px;
    text-align: right;
  }
  .person-name {
    font-family: "Yanone Kaffeesatz", sans-serif;
    font-size: 44px;
    color: var(--orange-light);
    line-height: 1;
  }
  .person-name .given { text-transform: uppercase; }
  .person-title {
    font-size: 12px;
    color: var(--orange-light);
    margin-top: 4px;
  }
  .contact {
    position: absolute;
    left: 282px;
    right: 36px;
    bottom: 28px;
    color: var(--white);
    font-size: 12px;
    line-height: 1.6;
  }
  .phone-pill {
    display: inline-block;
    margin: 8px 0 10px;
    padding: 2px 14px;
    border-radius: 14px;
    background: linear-gradient(180deg, var(--orange-light), var(--orange-dark));
    font-family: "Yanone Kaffeesatz", sans-serif;
    font-size: 24px;
    letter-spacing: 0.5px;
    color: var(--white);
  }
  .links { display: flex; flex-direction: column; gap: 3px; }
  .link { display: flex; align-items: center; gap: 8px; }
  .link-icon {
    flex: none;
    width: 14px; height: 14px; border-radius: 50%;
    background: var(--orange-light);
  }

  /* Back */
  .card-back {
    background: radial-gradient(ellipse at 50% 40%, var(--blue-mid) 0%, var(--blue-deep) 75%);
    display: flex;
    flex-direction: column;
    align-items: center;
    justify-content: center;
    color: var(--white);
  }
  .back-head { display: flex; flex-direction: column; align-items: flex-end; }
  .back-brand .brand-name { font-size: 52px; color: var(--blue-cyan); }
  .back-brand .brand-dot { width: 38px; height: 38px; background: var(--blue-cyan); }
  .back-tagline {
    font-size: 12px; font-style: italic; color: var(--ink-soft);
    margin: 4px 0 18px;
  }
  .services {
    display: flex;
    gap: 10px;
    padding: 5px 18px;
    border-radius: 14px;
    background: linear-gradient(180deg, var(--orange-light), var(--orange-dark));
    font-size: 13px;
    font-weight: 700;
  }
  .services .sep { opacity: 0.7; }
  .socials {
    display: flex;
    gap: 36px;
    margin-top: 14px;
    font-size: 12px;
    color: var(--ink-soft);
  }
</style>
</head>
<body>

  <section class="card card-front" aria-label="Card front">
    <svg class="front-art" viewBox="0 0 630 360" preserveAspectRatio="none" aria-hidden="true">
      <defs>
        <linearGradient id="orangePanel" x1="0" y1="0" x2="1" y2="1">
          <stop offset="0" stop-color="#d9641e"/>
          <stop offset="1" stop-color="#f3a037"/>
        </linearGradient>
      </defs>
      <path d="M0 0 H210 C270 110 270 250 225 360 H0 Z" fill="url(#orangePanel)"/>
      <path d="M210 0 C270 110 270 250 225 360" fill="none" stroke="#ffffff" stroke-width="7"/>
    </svg>

    <div class="brand">
      <div class="brand-row">
        <span class="brand-dot"></span>
        <span class="brand-name">Trelvan Media</span>
      </div>
      <p class="brand-tagline">Build your web presence</p>
    </div>

    <div class="person">
      <p class="person-name"><span class="given">Mark</span> Lenner</p>
      <p class="person-title">President/CEO</p>
    </div>

    <div class="contact">
      <p class="address">4315 W. Calloway Ave. Ste. 140, Tucson, AZ 85792</p>
      <p class="phone-local">520-381-7459</p>
      <span class="phone-pill">866-381-7459 (Toll Free)</span>
      <div class="links">
        <span class="link"><span class="link-icon"></span>mark@trelvanmedia.example</span>
        <span class="link"><span class="link-icon"></span>www.trelvanmedia.example</span>
      </div>
    </div>
  </section>

  <section class="card card-back" aria-label="Card back">
    <div class="back-head">
      <div class="brand-row back-brand">
        <span class="brand-dot"></span>
        <span class="brand-name">Trelvan Media</span>
      </div>
      <p class="back-tagline">Build your web presence</p>
    </div>
    <div class="services">
      <span>Web Design</span><span class="sep">|</span>
      <span>Internet Marketing</span><span class="sep">|</span>
      <span>Website Management</span>
    </div>
    <div class="socials">
      <span class="link"><span class="link-icon"></span>www.facebook.com/trelvanmedia</span>
      <span class="link"><span class="link-icon"></span>@trelvanmedia</span>
    </div>
  </section>

</body>
</html>
```